Rovelux

Hi everyone!

Looks like our project is more sophisticated than we expected. So good news - we increased the budget! and one of you will sure get the prize - no money back for us!

We are a young Russian company that specializes in in-taxi entertainment. We believe that our key strength is great attention to user experience. We've devoted much effort to improve ergonomics of our devices - tablet PCs that we install in the taxis. And yes, we enjoy to simplify things!

Now we need the most basic things - a logo and some staff for client meetings (primarily advertisers and ad agencies).

As for logo - we already have one engraved on the prototypes of our device (see attached file). This is one of the ideas (still far from perfect) - what we appreciate in it is minimalistic yet stylish approach.

As for "take it to the meeting stuff" we want to start with name card, pen and notepad (A4) that we will leave in clients's office, also as a reminder. Shall your have more smart ideas - always welcome!

As for logo and name cards - we would like to make an image of serious but modern company. Our design should communicate creativity and reliability. We believe that "to understand is to simplify" - minimalistic design is the most difficult one. Its better to work hard on fonts and arrangement, than put 10 variegated images.

SO THE TASK IS TO DESIGN:
- a logo
- a name card
- a note pad (great example in attachment)
- a pen

Shall you have more questions - please ask in comments.

We look forward to meeting like-minded fellows here!
Updates

Target Market(s)

Out target are:

- advertiser
- advertising agencies
- taxi passenger

Industry/Entity Type

It Company

Requirements
Must have
• font should be chosen very carefully
Nice to have
• classic minimalistic plain text only but very stylish name card is a dream of one of our co-founders:)
Should not have
• we do not want to have taxi-like colors and chess-boards. We are closer to "innovation", "entertainment", and "user experience", rather than "taxi".

```html
<!DOCTYPE html>
<html lang="en">
<head>
<meta charset="utf-8">
<title>Rovelux Notepad</title>
<link href="https://fonts.googleapis.com/css2?family=Open+Sans:wght@300;400&display=swap" rel="stylesheet">
<style>
  :root {
    --canvas: #ffffff;
    --paper: #ffffff;
    --brand: #4a6f8f;
    --ink: #2e5878;
    --rule: #e3e5e8;
    --box-edge: #dfe1e4;
    --dot: #cfd3d8;
    --chevron: #b5bcc4;
  }
  * { margin: 0; padding: 0; box-sizing: border-box; }
  html, body {
    width: 1200px; height: 1000px; overflow: hidden;
    background: var(--canvas);
    font-family: "Open Sans", Arial, sans-serif;
  }
  .sheet {
    position: absolute; left: 280px; top: 48px;
    width: 638px; height: 902px;
    background: var(--paper);
    box-shadow: 0 2px 14px rgba(0,0,0,0.22);
  }
  .brand-name {
    position: absolute; left: 45px; top: 22px;
    font-size: 46px; font-weight: 300; letter-spacing: 1px;
    color: var(--brand); line-height: 1;
  }
  .entry { position: absolute; left: 45px; width: 570px; height: 64px; }
  .entry-box {
    position: absolute; left: 0; top: 0; width: 68px; height: 54px;
    border: 1px solid var(--box-edge); border-radius: 10px;
  }
  .entry-rule {
    position: absolute; left: 68px; top: 27px; width: 492px; height: 1px;
    background: var(--rule);
  }
  .entry-dot {
    position: absolute; left: 560px; top: 25.5px; width: 4px; height: 4px;
    border: 1px solid var(--dot); border-radius: 50%;
  }
  .entry-subrule {
    position: absolute; left: 97px; top: 59px; width: 448px; height: 1px;
    background: var(--rule);
  }
  .contact {
    position: absolute; right: 30px; top: 863px;
    display: flex; gap: 9px; align-items: center;
    font-size: 9px; color: var(--ink); letter-spacing: 0.1px;
  }
  .contact .sep { color: var(--chevron); font-size: 8px; }
</style>
</head>
<body>
  <div class="sheet">
    <div class="brand-name">rovelux</div>

    <div class="entry" style="top:114px"><div class="entry-box"></div><div class="entry-rule"></div><div class="entry-dot"></div><div class="entry-subrule"></div></div>
    <div class="entry" style="top:178px"><div class="entry-box"></div><div class="entry-rule"></div><div class="entry-dot"></div><div class="entry-subrule"></div></div>
    <div class="entry" style="top:242px"><div class="entry-box"></div><div class="entry-rule"></div><div class="entry-dot"></div><div class="entry-subrule"></div></div>
    <div class="entry" style="top:306px"><div class="entry-box"></div><div class="entry-rule"></div><div class="entry-dot"></div><div class="entry-subrule"></div></div>
    <div class="entry" style="top:370px"><div class="entry-box"></div><div class="entry-rule"></div><div class="entry-dot"></div><div class="entry-subrule"></div></div>
    <div class="entry" style="top:434px"><div class="entry-box"></div><div class="entry-rule"></div><div class="entry-dot"></div><div class="entry-subrule"></div></div>
    <div class="entry" style="top:498px"><div class="entry-box"></div><div class="entry-rule"></div><div class="entry-dot"></div><div class="entry-subrule"></div></div>
    <div class="entry" style="top:562px"><div class="entry-box"></div><div class="entry-rule"></div><div class="entry-dot"></div><div class="entry-subrule"></div></div>
    <div class="entry" style="top:626px"><div class="entry-box"></div><div class="entry-rule"></div><div class="entry-dot"></div><div class="entry-subrule"></div></div>
    <div class="entry" style="top:690px"><div class="entry-box"></div><div class="entry-rule"></div><div class="entry-dot"></div><div class="entry-subrule"></div></div>
    <div class="entry" style="top:754px"><div class="entry-box"></div><div class="entry-rule"></div><div class="entry-dot"></div><div class="entry-subrule"></div></div>
    <div class="entry" style="top:818px"><div class="entry-box"></div><div class="entry-rule"></div><div class="entry-dot"></div></div>

    <div class="contact">
      <span>+7 55500123</span><span class="sep">›</span>
      <span>rovelux@rovelux.com</span><span class="sep">›</span>
      <span>www.rovelux.com</span>
    </div>
  </div>
</body>
</html>
```